Business Card Design

We need a design for business cards for our company. We have a logo. We teach EMT's and we are based out of Virginia. The information that will need to add would be, name, title, phone number, email, address. On the back of the business card would be "We help you, help others"

Target Market(s)

People that want to become EMT's

Colors

Designer to choose colors to be used in the design.

Requirements
Must have
• company logo

```html
<!DOCTYPE html>
<html lang="en">
<head>
<meta charset="utf-8">
<title>Field Ready Training – Business Card</title>
<link href="https://fonts.googleapis.com/css2?family=Source+Sans+3:wght@400;600&display=swap" rel="stylesheet">
<style>
  :root {
    --backdrop: #dcdddf;
    --card-dark: #212b36;
    --card-light: #ffffff;
    --brand-red: #e3233e;
    --line-grey: #9aa3ad;
    --text-muted: #7e8994;
    --text-slate: #5c6875;
    --label-grey: #444a50;
    --arrow-grey: #6e7378;
  }
  * { margin: 0; padding: 0; box-sizing: border-box; }
  html, body { width: 1200px; height: 1200px; overflow: hidden; }
  body {
    position: relative;
    background: var(--backdrop);
    font-family: "Source Sans 3", "Helvetica Neue", Arial, sans-serif;
  }
  .card {
    position: absolute;
    left: 361px;
    width: 474px;
    height: 269px;
    overflow: hidden;
    box-shadow: 0 14px 14px -6px rgba(0,0,0,0.45);
  }
  .card--front { top: 236px; background: var(--card-dark); }
  .card--back  { top: 532px; background: var(--card-light); }
  .card__stripes { position: absolute; inset: 0; width: 474px; height: 269px; }
  .wordmark {
    position: absolute;
    left: 60px;
    top: 66px;
    display: flex;
    align-items: center;
    gap: 12px;
  }
  .wordmark__dot {
    width: 26px; height: 26px; border-radius: 50%;
    background: var(--line-grey);
  }
  .wordmark__name {
    color: var(--brand-red);
    font-weight: 600;
    font-size: 29px;
    line-height: 0.95;
    letter-spacing: 0.5px;
    text-transform: uppercase;
  }
  .holder {
    position: absolute;
    right: 255px;
    top: 222px;
    text-align: right;
    color: var(--text-muted);
  }
  .holder__name { font-size: 14px; line-height: 17px; }
  .holder__title { font-size: 11px; line-height: 15px; margin-right: 4px; }
  .contact {
    position: absolute;
    left: 228px;
    top: 205px;
    list-style: none;
    color: var(--text-muted);
    font-size: 11px;
  }
  .contact__item { display: flex; align-items: center; gap: 6px; height: 17px; }
  .contact__item:nth-child(2) { padding-left: 14px; }
  .contact__item:nth-child(3) { padding-left: 24px; }
  .contact__icon { width: 11px; height: 11px; fill: var(--text-muted); flex: none; }
  .tagline {
    position: absolute;
    left: 178px;
    top: 142px;
    color: var(--text-slate);
    font-size: 15px;
  }
  .side-label {
    position: absolute;
    left: 898px;
    display: flex;
    align-items: center;
    gap: 6px;
    color: var(--label-grey);
    font-size: 15px;
  }
  .side-label--front { top: 358px; }
  .side-label--back  { top: 644px; }
  .side-label__arrow {
    width: 0; height: 0;
    border-top: 12px solid transparent;
    border-bottom: 12px solid transparent;
    border-right: 12px solid var(--arrow-grey);
  }
</style>
</head>
<body>

  <section class="card card--front">
    <svg class="card__stripes" viewBox="0 0 474 269" aria-hidden="true">
      <line x1="67" y1="-2" x2="104" y2="59" stroke="var(--brand-red)" stroke-width="4"/>
      <line x1="161" y1="134" x2="256" y2="271" stroke="var(--line-grey)" stroke-width="5"/>
    </svg>
    <div class="wordmark">
      <span class="wordmark__dot"></span>
      <span class="wordmark__name">Field Ready<br>Training</span>
    </div>
    <div class="holder">
      <p class="holder__name">Dana Whitfield, LCSW, LAADC</p>
      <p class="holder__title">Director &amp; Founder | Interventionist</p>
    </div>
    <ul class="contact">
      <li class="contact__item">
        <svg class="contact__icon" viewBox="0 0 24 24"><path d="M6.6 10.8a15.1 15.1 0 0 0 6.6 6.6l2.2-2.2a1 1 0 0 1 1-.25 11.4 11.4 0 0 0 3.6.57 1 1 0 0 1 1 1V20a1 1 0 0 1-1 1A17 17 0 0 1 3 4a1 1 0 0 1 1-1h3.5a1 1 0 0 1 1 1c0 1.25.2 2.45.57 3.57a1 1 0 0 1-.25 1z"/></svg>
        555-210-4187
      </li>
      <li class="contact__item">
        <svg class="contact__icon" viewBox="0 0 24 24"><path d="M2 5h20v14H2z M3.5 6.5 12 12.5l8.5-6z" fill-rule="evenodd"/></svg>
        dana@fieldready.com
      </li>
      <li class="contact__item">
        <svg class="contact__icon" viewBox="0 0 24 24"><path d="M12 2a7 7 0 0 0-7 7c0 5.2 7 13 7 13s7-7.8 7-13a7 7 0 0 0-7-7zm0 9.5A2.5 2.5 0 1 1 12 6.5a2.5 2.5 0 0 1 0 5z"/></svg>
        Suite 14, 80 Elm Street N.E., Riverton
      </li>
    </ul>
  </section>

  <section class="card card--back">
    <svg class="card__stripes" viewBox="0 0 474 269" aria-hidden="true">
      <line x1="67" y1="-2" x2="104" y2="59" stroke="var(--brand-red)" stroke-width="4"/>
      <line x1="186" y1="166" x2="256" y2="271" stroke="var(--line-grey)" stroke-width="5"/>
    </svg>
    <div class="wordmark">
      <span class="wordmark__dot"></span>
      <span class="wordmark__name">Field Ready<br>Training</span>
    </div>
    <p class="tagline">We help you, help others</p>
  </section>

  <div class="side-label side-label--front"><span class="side-label__arrow"></span>Front side</div>
  <div class="side-label side-label--back"><span class="side-label__arrow"></span>Back side</div>

</body>
</html>
```